Drinking and Driving course for the courts

Sophisitcated tri-fold brochure seen by judges, lawyers etc. People taking this course have been charged with drinking and driving (alcohol). Should be classy and upmarket. Please be creative like original brochure. Please use exact wording and in same order as brochure. Also please keep in approximately same place on brochure. Spelling and grammar should be exactly same as this document is already proof-read and checked by experts.

Target Market(s)

Judges, lawyers, court system.

Industry/Entity Type

Legal

Font styles to use
Serif

Requirements
Must have
• Creative and classy. Can look similar or same as original brochure. Should have pciture/graphic of car keys and drink
Nice to have
• A background graphic like in original brochure comes across very well. Subtle etc.
Should not have
• Does not need to have pictures of vehicles/cars. Definitely no brand names of cars or alcohol labels (or any kind).

```html
<!DOCTYPE html>
<html lang="en">
<head>
<meta charset="utf-8">
<title>Mindful Drive – Clearway Driving School</title>
<link rel="stylesheet" href="https://fonts.googleapis.com/css2?family=Anton&family=Archivo+Black&family=Cinzel:wght@400;700&family=Crimson+Text:ital,wght@0,400;1,400;1,600&display=swap">
<style>
  :root {
    --page: #e6dccb;
    --tan-light: #bb9a70;
    --tan: #a9835a;
    --brown-dark: #3e2718;
    --brown-deep: #2a180d;
    --brown-mid: #53372a;
    --cream: #f5ede1;
    --white: #ffffff;
    --gold: #d9b45e;
  }
  * { box-sizing: border-box; margin: 0; padding: 0; }
  html, body { width: 1200px; height: 800px; overflow: hidden; background: var(--page); }
  .canvas { position: relative; width: 1200px; height: 800px; }

  .panel {
    position: absolute; top: 40px; width: 340px; height: 720px; overflow: hidden;
    background: linear-gradient(180deg, var(--tan) 0%, var(--tan-light) 60%, var(--tan) 100%);
    box-shadow: 0 6px 18px rgba(60, 40, 20, .25);
  }
  .panel--back { left: 220px; }
  .panel--cover { left: 640px; }
  .abs { position: absolute; }
  .shape { position: absolute; left: 0; top: 0; }

  /* Back panel */
  .remote-icon { left: 22px; top: 28px; width: 84px; height: 72px; border-radius: 8px;
    background: linear-gradient(135deg, var(--brown-dark), var(--brown-mid)); }
  .remote-heading { left: 118px; top: 34px; font-family: "Archivo Black", sans-serif; font-size: 25px; line-height: 1.1; }
  .remote-heading .dark { color: var(--brown-dark); display: block; }
  .remote-heading .light { color: var(--white); display: block; }
  .online-illustration { left: 28px; top: 118px; width: 288px; height: 210px; border-radius: 26px;
    background: linear-gradient(160deg, #eef1f4 0%, #cfd8e6 55%, #7d95c4 100%); }
  .course-cost { left: 30px; top: 342px; width: 258px; height: 32px; border-radius: 6px; background: var(--cream);
    display: flex; align-items: center; padding: 0 4px; gap: 8px; }
  .course-cost__label { background: var(--brown-dark); color: var(--white); font-family: "Archivo Black", sans-serif;
    font-size: 11px; padding: 4px 7px; border-radius: 4px; }
  .course-cost__price { font-family: "Archivo Black", sans-serif; font-size: 15px; color: var(--tan); }
  .title-serif { font-family: "Cinzel", serif; color: var(--white); letter-spacing: 1px; }
  .title-bold { font-family: "Anton", sans-serif; color: var(--white); letter-spacing: 1px; }
  .back-title { left: 0; width: 340px; text-align: center; }
  .back-title.title-serif { top: 392px; font-size: 48px; }
  .back-title.title-bold { top: 440px; font-size: 66px; line-height: 1; }
  .school-name { font-family: "Archivo Black", sans-serif; color: var(--white); }
  .tagline-serif { font-family: "Crimson Text", serif; font-style: italic; color: var(--white); }
  .back-school { left: 0; width: 340px; top: 578px; text-align: center; font-size: 19px; }
  .back-tagline { left: 0; width: 340px; top: 606px; text-align: center; font-size: 17px; }
  .back-services { left: 0; width: 340px; top: 652px; text-align: center; font-size: 17px; line-height: 1.3; }

  /* Cover panel */
  .cover-title.title-serif { left: 34px; top: 22px; font-size: 46px; }
  .cover-title.title-bold { left: 62px; top: 70px; font-size: 78px; line-height: 1; }
  .drink-photo { left: 140px; top: 170px; width: 200px; height: 310px;
    background: radial-gradient(ellipse at 50% 45%, #f3e3a4 0%, var(--gold) 25%, #8a6227 55%, #2e1c0e 100%); }
  .course-summary { left: 10px; top: 212px; width: 170px; text-align: center; font-family: "Cinzel", serif;
    color: var(--white); font-size: 13px; line-height: 1.35; letter-spacing: .5px; }
  .course-summary hr { border: 0; border-top: 1px solid rgba(255,255,255,.75); margin: 8px 18px; }
  .cover-school { right: 14px; top: 396px; text-align: right; font-family: "Cinzel", serif; font-weight: 700;
    color: var(--white); font-size: 16px; line-height: 1.2; transform: rotate(-14deg); transform-origin: right top; }
  .cover-tagline { left: 0; width: 340px; top: 540px; text-align: center; font-family: "Archivo Black", sans-serif;
    font-size: 16px; color: var(--white); }
  .cover-services { left: 0; width: 340px; top: 588px; text-align: center; font-size: 18px; line-height: 1.3; }
  .cover-services b { font-family: "Archivo Black", sans-serif; font-style: normal; font-weight: 400; font-size: 15px; }
  .contact-strip { left: 0; top: 668px; width: 340px; height: 52px; background: var(--brown-deep);
    display: flex; align-items: center; }
  .contact-strip__phone { width: 150px; text-align: center; font-family: "Archivo Black", sans-serif; font-size: 17px;
    color: var(--white); border-right: 1px solid rgba(255,255,255,.5); }
  .contact-strip__web { flex: 1; padding-left: 10px; font-family: "Archivo Black", sans-serif; font-size: 9px;
    line-height: 1.5; color: var(--white); }
</style>
</head>
<body>
<main class="canvas">

  <section class="panel panel--back" aria-label="Back panel">
    <div class="abs remote-icon" role="img" aria-label="Icon of a monitor with a speech bubble"></div>
    <h2 class="abs remote-heading"><span class="dark">OFFERED</span><span class="light">REMOTELY!</span></h2>
    <div class="abs online-illustration" role="img" aria-label="Illustration of an online class with presenter and learner"></div>
    <div class="abs course-cost">
      <span class="course-cost__label">Course Cost:</span>
      <span class="course-cost__price">$775.00 + HST</span>
    </div>
    <p class="abs back-title title-serif">MINDFUL</p>
    <p class="abs back-title title-bold">DRIVE</p>
    <svg class="shape" width="340" height="720" viewBox="0 0 340 720" aria-hidden="true">
      <defs>
        <linearGradient id="backBand" x1="0" y1="0" x2="1" y2="0">
          <stop offset="0" stop-color="#2f1a0d"/><stop offset="1" stop-color="#4e3426"/>
        </linearGradient>
      </defs>
      <path d="M0,558 Q150,528 340,548 L340,720 L0,720 Z" fill="url(#backBand)"/>
    </svg>
    <p class="abs back-school school-name">Clearway Driving School</p>
    <p class="abs back-tagline tagline-serif">Guiding drivers well...for years!</p>
    <p class="abs back-services tagline-serif">For all your G License needs!<br>Beginner, Rehabilitation &amp; Remedial</p>
  </section>

  <section class="panel panel--cover" aria-label="Front cover">
    <p class="abs cover-title title-serif">MINDFUL</p>
    <p class="abs cover-title title-bold">DRIVE</p>
    <div class="abs drink-photo" role="img" aria-label="Photograph of a glass of whisky on ice beside car keys"></div>
    <svg class="shape" width="340" height="720" viewBox="0 0 340 720" aria-hidden="true">
      <defs>
        <linearGradient id="coverWave" x1="0" y1="0" x2="1" y2="1">
          <stop offset="0" stop-color="#4f3325"/><stop offset="1" stop-color="#331d10"/>
        </linearGradient>
      </defs>
      <path d="M0,200 Q110,150 190,205 Q225,300 195,420 Q170,490 90,505 L0,512 Z" fill="url(#coverWave)"/>
      <path d="M60,505 Q230,480 340,385 L340,445 Q230,510 0,520 L0,512 Z" fill="#3a2314"/>
      <path d="M0,524 Q230,515 340,448" fill="none" stroke="#ffffff" stroke-width="3"/>
    </svg>
    <div class="abs course-summary">
      A 1-DAY<br>EDUCATIONAL COURSE
      <hr>
      FOR THOSE<br>CHARGED WITH
      <hr>
      DRINKING<br>AND<br>DRIVING
      <hr>
    </div>
    <p class="abs cover-school">Clearway<br>Driving School</p>
    <p class="abs cover-tagline">Guiding drivers well...for years!</p>
    <p class="abs cover-services tagline-serif">For all your <b>G License</b> needs!<br>Beginner, Rehabilitation &amp; Remedial</p>
    <div class="abs contact-strip">
      <span class="contact-strip__phone">705-555-0142</span>
      <span class="contact-strip__web">www.clearwaydrivingschool.ca<br>info@clearwaydrivingschool.ca</span>
    </div>
  </section>

</main>
</body>
</html>
```